Business Card Design needed for start up company Halvora

In need of a new business card designed for a start up company based in Sydney, Halvora is a new start up innovative Company, our mission it to make property accessible for everyday Australian and to become the leading Real Estate platform in Australia. We want it to be fresh and clean.

Industry/Entity Type

Financial

Contact Information for Business Card

Section for Name
Section for Title

HALVORA - The Strength of Pooling
Mobile:
Direct:

Font styles to use
Sans Serif

Colors
33a6d7
0692cd
0255a3
ffffff

Requirements
Must have
• Logo, all business card details

```html
<!DOCTYPE html>
<html lang="en">
<head>
<meta charset="utf-8">
<title>Halvora Business Card</title>
<link rel="stylesheet" href="https://fonts.googleapis.com/css2?family=Jost:ital,wght@0,400;0,600;0,700;1,400&display=swap">
<style>
  :root {
    --sky: #33a6d7;
    --azure: #2a9bd8;
    --cerulean: #0692cd;
    --navy: #0255a3;
    --navy-deep: #1d3f7e;
    --white: #ffffff;
    --stage: #e8ebef;
  }
  * { box-sizing: border-box; margin: 0; padding: 0; }
  html, body { width: 1200px; height: 911px; overflow: hidden; }
  body {
    background: var(--stage);
    font-family: "Jost", sans-serif;
    display: flex;
    align-items: center;
    justify-content: center;
    gap: 40px;
  }
  .card {
    position: relative;
    width: 540px;
    height: 310px;
    border-radius: 22px;
    overflow: hidden;
    box-shadow: 0 6px 18px rgba(0,0,0,0.18);
  }
  .card-front { background: var(--white); }
  .front-shapes { position: absolute; inset: 0; }
  .brand {
    position: absolute;
    display: flex;
    align-items: center;
    gap: 10px;
    font-weight: 700;
    letter-spacing: 1px;
    line-height: 1;
  }
  .brand-dot { border-radius: 50%; flex: none; }
  .card-front .brand { left: 34px; top: 24px; font-size: 40px; color: var(--navy); }
  .card-front .brand-dot { width: 44px; height: 44px; background: var(--sky); }
  .contact {
    position: absolute;
    left: 30px;
    bottom: 16px;
    color: var(--white);
    font-size: 12.5px;
    line-height: 1.25;
  }
  .contact-name { color: var(--sky); font-weight: 700; font-size: 18px; letter-spacing: 0.5px; }
  .contact-title { font-size: 14px; margin-bottom: 4px; }
  .contact-address { margin-bottom: 4px; }
  .contact-line { display: flex; align-items: center; gap: 8px; }
  .contact-icon { width: 11px; height: 11px; flex: none; }
  .card-back { background: var(--azure); }
  .card-back .brand { left: 90px; top: 118px; font-size: 66px; color: var(--white); }
  .card-back .brand-dot { width: 74px; height: 74px; background: var(--white); }
  .tagline {
    position: absolute;
    left: 96px;
    top: 204px;
    color: var(--white);
    font-style: italic;
    font-size: 15px;
  }
</style>
</head>
<body>
  <section class="card card-front" aria-label="Card front">
    <svg class="front-shapes" viewBox="0 0 540 310" width="540" height="310" aria-hidden="true">
      <path d="M0 104 Q300 130 540 16 L540 28 Q300 142 0 116 Z" fill="var(--sky)"/>
      <path d="M0 121 Q300 148 540 32 L540 310 L0 310 Z" fill="var(--navy-deep)"/>
    </svg>
    <div class="brand"><span class="brand-dot"></span><span class="brand-name">HALVORA</span></div>
    <div class="contact">
      <div class="contact-name">MARA ELLISON</div>
      <div class="contact-title">CEO/FOUNDER</div>
      <div class="contact-address">214 Wattle Crescent<br>Sydney, NSW 2000</div>
      <div class="contact-line">
        <svg class="contact-icon" viewBox="0 0 12 12"><path d="M2 1 L4.5 1 L5.5 3.5 L4 4.5 Q5 7 7.5 8 L8.5 6.5 L11 7.5 L11 10 Q6 11 2 6 Q1 3.5 2 1Z" fill="var(--sky)"/></svg>
        <span>612 480 1937</span>
      </div>
      <div class="contact-line">
        <svg class="contact-icon" viewBox="0 0 12 12"><rect x="3" y="0.5" width="6" height="11" rx="1" fill="none" stroke="var(--sky)" stroke-width="1.3"/></svg>
        <span>614 275 8830</span>
      </div>
      <div class="contact-line">
        <svg class="contact-icon" viewBox="0 0 12 12"><rect x="0.7" y="2.5" width="10.6" height="7" fill="none" stroke="var(--sky)" stroke-width="1.2"/><path d="M0.7 2.5 L6 7 L11.3 2.5" fill="none" stroke="var(--sky)" stroke-width="1.2"/></svg>
        <span>mara@halvora.com</span>
      </div>
      <div class="contact-line">
        <svg class="contact-icon" viewBox="0 0 12 12"><circle cx="6" cy="6" r="5" fill="none" stroke="var(--sky)" stroke-width="1.2"/><path d="M1 6 H11 M6 1 Q3 6 6 11 M6 1 Q9 6 6 11" fill="none" stroke="var(--sky)" stroke-width="1"/></svg>
        <span>www.halvora.com</span>
      </div>
    </div>
  </section>

  <section class="card card-back" aria-label="Card back">
    <div class="brand"><span class="brand-dot"></span><span class="brand-name">HALVORA</span></div>
    <p class="tagline">The Strength of Pooling</p>
  </section>
</body>
</html>
```